Letterhead for a German Distribution/Manufacturing Company

We need a professional Letterhead in a unique Design.
not to playful.
The Letterhead has to show show that we are a international company with headquater in Germany.
all details like adress, Vat Tax Number, Bank Accout, Eori, email, Company number has to be on the Letterhead.
for example use: VAT TAX DE5470318 Bank Account: Kestrel Bank IBAN DE412058731ß204683 Swift: MORV0417352 EORI 3150428697 Company Number: HRB 51806 Adress: VOLMINTA UG Ahornweg 7 Postal Code 06384 City Lindenfeld Country: Germany Email: info@volminta-example.com
the design can be colored but doesnt have to be
Industry/Entity Type
Manufacturing and international distribution
Requirements
Must have
- show that we are a international company with headquater in Germany. our company infos and logo

```html
<!DOCTYPE html>
<html lang="en">
<head>
<meta charset="utf-8">
<title>VOLMINTA Letterhead</title>
<link rel="stylesheet" href="https://fonts.googleapis.com/css2?family=Poppins:wght@400;500;600&display=swap">
<style>
  :root{
    --bg:#e4e4e4;
    --paper:#ffffff;
    --ink:#2e2e2e;
    --body:#4a4a4a;
    --accent:#e8194a;
    --orange:#ff5a36;
    --purple:#6d1aa6;
    --white:#ffffff;
    --flag-black:#111111;
    --flag-red:#e3101a;
    --flag-gold:#ffcc00;
  }
  *{margin:0;padding:0;box-sizing:border-box}
  html,body{width:672px;height:1200px;overflow:hidden;background:var(--bg)}
  body{position:relative;font-family:"Poppins",sans-serif;color:var(--ink)}
  .letterhead{
    position:absolute;left:24px;top:196px;width:624px;height:807px;
    background:var(--paper);overflow:hidden;
    box-shadow:0 10px 24px rgba(0,0,0,.18);
  }
  .abs{position:absolute}
  .brand{left:59px;top:40px;display:flex;align-items:center;gap:8px}
  .brand-dot{width:26px;height:26px;border-radius:50%;background:var(--ink)}
  .brand-name{font-size:27px;font-weight:400;color:var(--ink);letter-spacing:.5px;line-height:1}
  .tagline{right:84px;top:48px;text-align:right;font-size:10.6px;font-weight:600;line-height:12.5px;text-transform:uppercase;letter-spacing:.2px}
  .flag{left:542px;top:48px;width:24px;height:24px}
  .header-decor{
    left:0;top:96px;width:624px;height:40px;
    background:linear-gradient(90deg,rgba(109,26,166,.16),rgba(255,90,54,.16) 50%,rgba(232,25,74,.16));
  }
  .recipient-label{left:62px;top:175px;font-size:8.5px;font-weight:600}
  .recipient-name{left:62px;top:185px;font-size:17px;font-weight:500;color:var(--accent)}
  .letter-body{left:62px;top:214px;width:501px;font-size:9.85px;line-height:13.8px;color:var(--body);text-align:justify}
  .letter-body p{margin-bottom:13.8px}
  .closing{right:61px;top:586px;font-size:10px;color:var(--body)}
  .signature{left:394px;top:603px;width:169px;height:53px;border-radius:4px;
    background:linear-gradient(90deg,rgba(232,25,74,.10),rgba(232,25,74,.18))}
  .footer-decor{
    left:0;top:690px;width:399px;height:117px;
    background:linear-gradient(90deg,#f3284f,var(--orange) 50%,#e3585c 78%,#8a2aa8);
  }
  .contact{left:59px;font-size:10.2px;font-weight:500;color:var(--white);line-height:12.5px;display:flex;gap:5px}
  .contact svg{width:9px;height:9px;flex:none;margin-top:2px}
  .contact.address{top:720px}
  .contact.email{top:754px}
  .contact.web{top:770px}
  .company-details{right:61px;top:702px;text-align:right;font-size:9px;line-height:12.9px;color:var(--ink);font-weight:500}
  .company-details .label{color:var(--accent)}
</style>
</head>
<body>
<main class="letterhead">
  <header>
    <div class="abs brand"><span class="brand-dot"></span><span class="brand-name">VOLMINTA</span></div>
    <div class="abs tagline">International company with headquater<br>in Germany</div>
    <svg class="abs flag" viewBox="0 0 24 24" aria-label="Flag of Germany">
      <defs><clipPath id="flag-clip"><circle cx="12" cy="12" r="12"/></clipPath></defs>
      <g clip-path="url(#flag-clip)">
        <rect width="24" height="8" fill="var(--flag-black)"/>
        <rect y="8" width="24" height="8" fill="var(--flag-red)"/>
        <rect y="16" width="24" height="8" fill="var(--flag-gold)"/>
      </g>
    </svg>
    <div class="abs header-decor" role="img" aria-label="Decorative header divider in purple, orange and red tones"></div>
  </header>

  <div class="abs recipient-label">To</div>
  <div class="abs recipient-name">John Doe</div>

  <article class="abs letter-body">
    <p>It is a long established fact that a reader will be distracted by the readable content of a page when looking at its layout. The point of using Lorem Ipsum is that it has a more-or-less normal distribution of letters, as opposed to using 'Content here, content here', making it look like readable English. Many desktop publishing packages and web page editors now use Lorem Ipsum as their default model text, and a search for 'lorem ipsum' will uncover many web sites still in their infancy. Various versions have evolved over the years, sometimes by accident, sometimes on purpose (injected humour and the like</p>
    <p>Contrary to popular belief, Lorem Ipsum is not simply random text. It has roots in a piece of classical Latin literature from 45 BC, making it over 2000 years old. Harold Wendell, a Latin professor at Ashgrove College in Virginia, looked up one of the more obscure Latin words, consectetur, from a Lorem Ipsum passage, and going through the cites of the word in classical literature, discovered the undoubtable source. Lorem Ipsum comes from sections 1.10.32 and 1.10.33 of "de Finibus Bonorum et Malorum" (The Extremes of Good and Evil) by Marcus Tullo, written in 45 BC. This book is a treatise on the theory of ethics, very popular during the Renaissance. The first line of Lorem Ipsum, "Lorem ipsum dolor sit amet..", comes from a line in section 1.10.32.</p>
    <p>The standard chunk of Lorem Ipsum used since the 1500s is reproduced below for those interested. Sections 1.10.32 and 1.10.33 from "de Finibus Bonorum et Malorum" by Marcus Tullo are also reproduced in their exact original form, accompanied by English versions from the 1914 translation by H. Brantley</p>
    <p>College in Virginia, looked up one of the more obscure Latin words, consectetur, from a Lorem Ipsum passage, and going through the cites of the word in classical literature, discovered the undoubtable source. Lorem Ipsum comes from sections 1.10.32 and 1.10.33 of "de Finibus Bonorum et Malorum" (The Extremes of Good and Evil) by Marcus Tullo, written in 45 BC. This book is a treatise on the theory of ethics, very popular during the Renaissance. The first line of Lorem Ipsum, "Lorem ipsum dolor sit amet</p>
  </article>

  <div class="abs closing">Sincerely Yours</div>
  <div class="abs signature" role="img" aria-label="Handwritten signature of the sender"></div>

  <footer>
    <div class="abs footer-decor" role="img" aria-label="Decorative footer band in red, orange and purple tones"></div>

    <div class="abs contact address">
      <svg viewBox="0 0 10 10"><path d="M5 0.5a3.3 3.3 0 0 0-3.3 3.3C1.7 6.3 5 9.5 5 9.5s3.3-3.2 3.3-5.7A3.3 3.3 0 0 0 5 .5z" fill="var(--white)"/><circle cx="5" cy="3.8" r="1.2" fill="#f3284f"/></svg>
      <span>VOLMINTA UG Ahornweg 7 Postal Code<br>06384 City Lindenfeld Country</span>
    </div>
    <div class="abs contact email">
      <svg viewBox="0 0 10 10"><rect x=".5" y="2" width="9" height="6.5" fill="var(--white)"/><path d="M.7 2.3 5 5.6l4.3-3.3" fill="none" stroke="#f3284f" stroke-width=".8"/></svg>
      <span>info@volminta-example.com</span>
    </div>
    <div class="abs contact web">
      <svg viewBox="0 0 10 10" fill="none" stroke="var(--white)" stroke-width=".8"><circle cx="5" cy="5" r="4.2"/><ellipse cx="5" cy="5" rx="1.8" ry="4.2"/><path d="M.8 5h8.4M1.6 3h6.8M1.6 7h6.8"/></svg>
      <span>www.volminta-example.com</span>
    </div>

    <div class="abs company-details">
      <div><span class="label">VAT TAX</span> | DE5470318</div>
      <div><span class="label">Bank Account</span> | Kestrel Bank</div>
      <div><span class="label">IBAN</span> | DE412058731ß204683</div>
      <div><span class="label">Swift</span> | MORV0417352</div>
      <div><span class="label">EORI</span> &nbsp;| 3150428697</div>
      <div><span class="label">Company Number</span> &nbsp;| HRB 51806</div>
    </div>
  </footer>
</main>
</body>
</html>
```